Corvana Tongue Works, LLC

We need a business card that includes information about our business and conveys a reliable business that provides document translation services and interpreters for a variety of corporate and individual clients. We want to come across as professional, reliable, yet approachable. It should include the following on one side:

ESL / ENL Language Classes, Private Lessons, and Online Tutors
PLEXA Training and Testing
Translating & Interpreting Services
Contact us about Over-the-Phone Interpreting in over 200 languages
24/7/365
www.corvanatongue.example

The other side should include (555) 481-3062

Rhoda Pelling, President
482 Garnet Ave., Ste. 219
Indianapolis, IN 40917

Please add USA as part of the address. Also, please add rmpelling@corvanatongueworks.example as the e-mail address. Thank you.

Target Market(s)

Business professionals, their families, the international community

Industry/Entity Type

Business

Contact Information for Business Card

24/7/365
www.corvanatongue.example

(555) 481-3062

Rhoda Pelling, President
482 Garnet Ave., Ste. 219
Indianapolis, IN 40917
USA

Font styles to use
Sans Serif

Colors

Designer to choose colors to be used in the design.

Requirements
Must have
• See project description
• e-mail address and web address
• Phone number
Nice to have
• a globe
• physical address
Should not have
• Should not have the same color scheme as other agencies in our market in Indiana unless it is blue and black. No purple or yellow.

```html
<!DOCTYPE html>
<html lang="en">
<head>
<meta charset="utf-8">
<title>Corvana Tongue Works – Business Card</title>
<link rel="stylesheet" href="https://fonts.googleapis.com/css2?family=Lato:wght@400;700&display=swap">
<style>
  :root {
    --backdrop: #c1c1c1;
    --card-white: #ffffff;
    --brand-blue: #2196d6;
    --brand-blue-deep: #1e8dcc;
    --ink: #111111;
    --text-white: #ffffff;
  }
  * { margin: 0; padding: 0; box-sizing: border-box; }
  html, body { width: 1200px; height: 900px; overflow: hidden; }
  body {
    background: var(--backdrop);
    font-family: "Lato", sans-serif;
    position: relative;
  }
  .card {
    position: absolute;
    top: 306px;
    height: 272px;
    box-shadow: 2px 3px 5px rgba(0,0,0,0.35);
    overflow: hidden;
  }
  .card-front { left: 149px; width: 439px; background: var(--card-white); }
  .card-back {
    left: 608px; width: 441px;
    background: linear-gradient(180deg, var(--brand-blue) 0%, var(--brand-blue-deep) 100%);
    color: var(--text-white);
  }
  .corner-mark { position: absolute; left: 0; top: 25px; }
  .person { position: absolute; left: 36px; top: 30px; }
  .person-name {
    color: var(--brand-blue); font-weight: 700; font-size: 15.5px;
    letter-spacing: 0.2px; text-transform: uppercase; line-height: 18px;
  }
  .person-title { color: var(--ink); font-size: 12.5px; line-height: 16px; }
  .brand { position: absolute; left: 202px; top: 64px; display: flex; align-items: center; }
  .brand-dot {
    width: 90px; height: 90px; border-radius: 50%;
    background: var(--brand-blue); flex: none;
  }
  .brand-name {
    margin-left: 8px; color: var(--ink); font-size: 22px; line-height: 27px; font-weight: 400;
  }
  .contact { position: absolute; left: 20px; top: 194px; font-size: 13px; color: var(--ink); }
  .contact-row { display: flex; align-items: center; height: 18px; white-space: nowrap; }
  .contact-row svg { margin-right: 4px; flex: none; }
  .address {
    position: absolute; right: 24px; top: 188px; text-align: right;
    font-size: 13px; line-height: 18px; color: var(--ink);
  }
  .bottom-band { position: absolute; left: 0; bottom: 0; }
  .services { position: absolute; left: 40px; top: 42px; list-style: none; }
  .services li {
    position: relative; padding-left: 16px; font-size: 17px; line-height: 23.6px;
  }
  .services li::before {
    content: ""; position: absolute; left: 1px; top: 7px;
    width: 9px; height: 9px; border-radius: 50%; background: var(--text-white);
  }
  .availability {
    position: absolute; left: 40px; right: 29px; top: 204px;
    display: flex; align-items: center; gap: 8px;
    font-size: 17px; font-weight: 700;
  }
  .availability::before, .availability::after {
    content: ""; flex: 1; height: 1px; background: rgba(255,255,255,0.7);
  }
  .web-address {
    position: absolute; left: 40px; right: 29px; top: 226px;
    text-align: center; font-size: 17.5px; font-weight: 700;
  }
</style>
</head>
<body>
  <section class="card card-front">
    <svg class="corner-mark" width="30" height="40" viewBox="0 0 30 40" aria-hidden="true">
      <polygon points="0,0 12,0 17,38 0,38" fill="var(--ink)"/>
      <polygon points="12,0 28,0 28,38 17,38" fill="var(--brand-blue)"/>
    </svg>
    <div class="person">
      <p class="person-name">Rhoda Pelling</p>
      <p class="person-title">President</p>
    </div>
    <div class="brand">
      <div class="brand-dot"></div>
      <p class="brand-name">Corvana<br>Tongue<br>Works, LLC</p>
    </div>
    <div class="contact">
      <div class="contact-row">
        <svg width="16" height="16" viewBox="0 0 16 16" aria-hidden="true">
          <circle cx="8" cy="8" r="8" fill="var(--brand-blue)"/>
          <path d="M4.5 6.5 Q4.5 4.8 8 4.8 Q11.5 4.8 11.5 6.5 L10 7 L9.5 6 L6.5 6 L6 7 Z M5 8 H11 V11 H5 Z" fill="#fff"/>
        </svg>
        <span>(555) 481-3062</span>
      </div>
      <div class="contact-row">
        <svg width="16" height="16" viewBox="0 0 16 16" aria-hidden="true">
          <circle cx="8" cy="8" r="8" fill="var(--brand-blue)"/>
          <circle cx="8" cy="8" r="4" fill="none" stroke="#fff" stroke-width="1.2"/>
          <path d="M4 8 H12 M8 4 Q5.8 8 8 12 M8 4 Q10.2 8 8 12" fill="none" stroke="#fff" stroke-width="0.9"/>
        </svg>
        <span>www.corvanatongue.example</span>
      </div>
      <div class="contact-row">
        <svg width="16" height="16" viewBox="0 0 16 16" aria-hidden="true">
          <circle cx="8" cy="8" r="8" fill="var(--brand-blue)"/>
          <rect x="4" y="5" width="8" height="6" fill="#fff"/>
          <path d="M4 5 L8 8.3 L12 5" fill="none" stroke="var(--brand-blue)" stroke-width="0.9"/>
        </svg>
        <span>rmpelling@corvanatongueworks.example</span>
      </div>
    </div>
    <div class="address">
      <p>482 Garnet Ave., Ste. 219</p>
      <p>Indianapolis, IN 40917 USA</p>
    </div>
    <svg class="bottom-band" width="439" height="20" viewBox="0 0 439 20" aria-hidden="true">
      <polygon points="0,6 219,6 212,20 0,20" fill="var(--ink)"/>
      <polygon points="220,0 439,0 439,20 206,20" fill="var(--brand-blue)"/>
    </svg>
  </section>

  <section class="card card-back">
    <ul class="services">
      <li>ESL / ENL Language Classes,<br>Private Lessons, and Online Tutors</li>
      <li>PLEXA Training and Testing</li>
      <li>Translating &amp; Interpreting Services</li>
      <li>Contact us about Over-the-Phone<br>Interpreting in over 200 languages</li>
    </ul>
    <p class="availability">24/7/365</p>
    <p class="web-address">www.corvanatongue.example</p>
  </section>
</body>
</html>
```